Strategy and Technology Consulting - Our Story and Values Page

Interior Page design – Our History and Our Values

Our homepage has been designed and we are looking for a design for one of the interior pages. This interior page tells the story of Our History and Our Values

Because the homepage has been designed, we would like this interior page to reflect the design of the homepage without being a mirror image of the homepage.

This site will be implemented in WordPress using the Elementor framework.

Font: Poppins medium and Poppins dark
Illustrations: Our homepage illustrations were designed by “Brelin 1974” on Quillmark. Compatible original or stock illustrations are welcome. Stock photography is also welcome. Brelin is also available through Brelin Tosamek on Ravolo

Uploaded Files
• Homepage design – this is the design we will use for our homepage. Contest entries should reflect this basic style but should be distinctly different from the homepage.
• Our History and Our Values – Wireframe – the basic layout of the page we are looking for.
• Our History and Our Values – Word document with the text supporting the wireframe.
• Color Palette – please use colors compatible with the palette attached.

Our Story - timeline
There is a timeline element in the wireframe. The wireframe displays this as a series of chevrons (arrows), but it does not need to be. Creativity in display of the timeline is appreciated.

Our Values
If you look at the Word document, you will see that there are a lot of words on the page. The winning design will present the information in a way that engages the user without overwhelming them with too much to read. For example, they may click on a value and see more information.

Target Market(s)

CIO's and Technology Executives

Number of Pages Required

1 page

Font styles to use
Sans Serif
Other font styles liked:
• Poppin

Requirements
Must have
• A timeline element, all of our values
Nice to have
• Clever timeline display

```html
<!DOCTYPE html>
<html lang="en">
<head>
<meta charset="utf-8">
<title>Veltrano – Our Story and Values</title>
<link href="https://fonts.googleapis.com/css2?family=Poppins:wght@400;500;600;700&display=swap" rel="stylesheet">
<style>
:root{
  --slate:#46526a;
  --slate-dark:#333d50;
  --slate-deep:#2a3242;
  --wave:#5c6880;
  --yellow:#f3b71e;
  --light:#eceff3;
  --panel:#f4f5f7;
  --white:#ffffff;
  --ink:#2b2f36;
  --muted:#5a6170;
}
*{box-sizing:border-box;margin:0;padding:0}
html,body{width:1200px;height:3036px;overflow:hidden}
body{font-family:'Poppins',sans-serif;color:var(--ink);background:var(--light);position:relative}
.header{position:absolute;top:0;left:0;width:1200px;height:64px;background:var(--white);display:flex;align-items:center;padding:0 48px;justify-content:space-between;box-shadow:0 2px 8px rgba(0,0,0,.08);z-index:3}
.brand{font-size:30px;font-weight:500;color:var(--slate);display:flex;align-items:center;gap:8px;letter-spacing:.5px}
.brand-dot{width:12px;height:12px;border-radius:50%;background:var(--yellow)}
.nav{display:flex;align-items:center;gap:26px;font-size:12px;font-weight:600;color:var(--slate)}
.btn{background:var(--yellow);color:var(--white);font-weight:600;font-size:12px;padding:10px 22px;border-radius:20px;border:none}
.story{position:absolute;top:64px;left:0;width:1200px;height:860px;background:var(--slate);overflow:hidden}
.waves{position:absolute;left:0;bottom:0}
.section-title{position:absolute;left:120px;font-size:26px;font-weight:700;color:var(--white);letter-spacing:.5px}
.timeline{position:absolute;top:180px;left:120px;width:968px;height:180px;background:var(--white);border-radius:14px;box-shadow:0 8px 24px rgba(0,0,0,.25);display:grid;grid-template-columns:1fr 1fr 1fr;overflow:hidden}
.era{padding:0 22px}
.era+.era{border-left:1px solid #d9dde3}
.era h3{font-size:18px;font-weight:500;text-align:center;height:50px;line-height:50px;border-bottom:4px solid var(--yellow);position:relative}
.era h3::after{content:"";position:absolute;left:-6px;bottom:-9px;width:14px;height:14px;border-radius:50%;background:var(--yellow)}
.era ul{list-style:none;padding-top:14px;font-size:13px;line-height:1.5}
.era li{padding-left:16px;position:relative}
.era li::before{content:"";position:absolute;left:0;top:7px;width:7px;height:7px;border-radius:50%;background:var(--yellow)}
.era li.sub{padding-left:32px}
.era li.sub::before{left:16px;width:7px;height:2px;top:10px;border-radius:0;background:var(--ink)}
.values-title{position:absolute;top:756px;left:120px;font-size:26px;font-weight:700;color:var(--slate);z-index:2}
.values{position:absolute;top:806px;left:120px;width:968px;background:var(--white);border-radius:14px;box-shadow:0 8px 24px rgba(0,0,0,.12);overflow:hidden;z-index:2}
.value{padding:22px 28px 24px;height:202px}
.value:nth-child(even){background:var(--panel)}
.value-head{display:flex;align-items:center;gap:14px;margin-bottom:12px}
.value-icon{width:34px;height:34px;border-radius:8px;background:linear-gradient(135deg,var(--yellow),#e08a2b)}
.value h4{font-size:18px;font-weight:600}
.value p{font-size:14px;line-height:1.6;color:var(--muted)}
.lower{position:absolute;top:2150px;left:0;width:1200px;height:886px}
.newsletter{position:absolute;top:2300px;left:120px;width:960px;height:176px;background:var(--yellow);border-radius:88px;display:flex;align-items:center;justify-content:space-between;padding:0 70px;z-index:2}
.newsletter h2{font-size:30px;font-weight:700;color:var(--white)}
.newsletter p{font-size:12px;color:var(--white);max-width:340px;margin-top:8px;font-weight:500}
.subscribe{width:340px;height:44px;background:var(--white);border-radius:22px;display:flex;align-items:center;justify-content:space-between;padding:0 6px 0 22px;font-size:12px;color:#999}
.subscribe span.go{width:32px;height:32px;border-radius:50%;background:var(--yellow)}
.footer{position:absolute;top:2620px;left:120px;width:960px;display:grid;grid-template-columns:360px 180px 240px 180px;color:var(--white);z-index:2}
.footer .brand{color:var(--white);font-size:44px}
.socials{display:flex;gap:10px;margin:20px 0 0 34px}
.socials span{width:30px;height:30px;border-radius:50%;background:rgba(255,255,255,.85)}
.footer .btn{display:inline-block;margin:20px 0 0 60px;font-size:10px}
.footer h5{font-size:16px;font-weight:600;margin-bottom:14px}
.footer ul{list-style:none;font-size:11px;line-height:2.2;color:#d6dbe4}
.footer li::before{content:"› ";color:var(--yellow)}
.contact li::before{content:""}
.contact li{display:flex;gap:10px;line-height:1.4;margin-bottom:12px}
.contact i{width:14px;height:14px;border-radius:3px;background:var(--yellow);flex:none;margin-top:2px}
.copyright{position:absolute;bottom:0;left:0;width:1200px;height:56px;background:var(--slate-deep);color:#e3e6ec;font-size:12px;display:flex;align-items:center;justify-content:center;z-index:2}
.chat{position:absolute;right:16px;bottom:60px;width:40px;height:40px;border-radius:50%;background:var(--yellow);z-index:3}
</style>
</head>
<body>
<header class="header">
  <div class="brand"><span class="brand-dot"></span>Veltrano</div>
  <nav class="nav"><span>AI</span><span>ABOUT US ▾</span><span>SERVICES ▾</span><span>INSIGHTS ▾</span><span>JOIN US ▾</span><span class="btn">CONTACT US</span></nav>
</header>

<section class="story">
  <h2 class="section-title" style="top:110px">OUR STORY</h2>
  <div class="timeline">
    <div class="era"><h3>2017 – 2019</h3><ul>
      <li>Growth Strategy Focus</li><li>Consistent, Modest Growth</li><li>Preliminary Focus on Technology</li><li>Funded implementing strategy is hard</li></ul></div>
    <div class="era"><h3>2020 – 2021</h3><ul>
      <li>Pandemic Pauses Growth</li><li>Rethinking</li><li class="sub">the business model</li><li class="sub">the delivery model</li></ul></div>
    <div class="era"><h3>2022 and Onward</h3><ul>
      <li>Leadership Team for Focus on Essential Areas</li><li>Rapid Growth</li><li>Customer Success</li></ul></div>
  </div>
  <svg class="waves" width="1200" height="420" viewBox="0 0 1200 420" aria-hidden="true">
    <path d="M0 120 C250 40 420 260 700 170 C930 95 1050 150 1200 60 L1200 420 L0 420Z" fill="var(--wave)" opacity=".6"/>
    <path d="M0 250 C260 160 460 330 760 250 C960 200 1080 230 1200 180 L1200 420 L0 420Z" fill="#7f8aa0" opacity=".5"/>
    <path d="M0 330 C300 270 520 390 820 330 C1000 295 1100 320 1200 300 L1200 420 L0 420Z" fill="var(--light)"/>
  </svg>
</section>

<h2 class="values-title">OUR VALUES</h2>
<div class="values">
  <div class="value"><div class="value-head"><div class="value-icon" role="img" aria-label="Illustration of people representing human value"></div><h4>The Value of Every Human. Regardless.</h4></div>
    <p>Each person's unique experiences and perspectives add vibrant hues to the tapestry of our shared existence. In a world where diversity paints the canvas of humanity, true beauty is found in recognizing the inherent and incalculable value of every human being.</p></div>
  <div class="value"><div class="value-head"><div class="value-icon" role="img" aria-label="Illustration representing collaboration"></div><h4>Collaboration</h4></div>
    <p>Collaboration in work transforms individual endeavors into symphonies of collective achievement. Through collaboration, diverse talents converge, fostering a rich exchange of ideas that amplifies creativity, accelerates progress, and brings forth solutions beyond what a single mind could conceive.</p></div>
  <div class="value"><div class="value-head"><div class="value-icon" role="img" aria-label="Illustration representing passion"></div><h4>Passion</h4></div>
    <p>Passion infuses our work with energy, transforming routine tasks into opportunities for creativity and innovation. Fueled by passion, individuals become unstoppable forces, driven to overcome challenges and achieve remarkable outcomes that benefit them and inspire those around them.</p></div>
  <div class="value"><div class="value-head"><div class="value-icon" role="img" aria-label="Illustration representing excellence"></div><h4>Excellence</h4></div>
    <p>Excellence isn't a destination; it's a continuous journey of refinement and growth. Striving for excellence cultivates a culture of continuous improvement, fostering innovation, credibility, and a lasting impact that resonates far beyond the immediate task.</p></div>
  <div class="value"><div class="value-head"><div class="value-icon" role="img" aria-label="Illustration representing tenacity"></div><h4>Tenacity</h4></div>
    <p>Tenacity is the unwavering anchor that keeps us grounded amidst adversity, propelling us forward when faced with obstacles. The resilience to persist, adapt, and learn from setbacks leads to the mastery of skills and the fulfillment of ambitious goals.</p></div>
  <div class="value"><div class="value-head"><div class="value-icon" role="img" aria-label="Illustration representing a solution mindset"></div><h4>Solution Mindset</h4></div>
    <p>A solution mindset is the compass that directs our focus from problems to possibilities. It empowers us to navigate challenges with a proactive mindset, igniting a journey of exploration and innovation that not only resolves issues but also paves the way for continuous growth and success.</p></div>
  <div class="value"><div class="value-head"><div class="value-icon" role="img" aria-label="Illustration representing generosity"></div><h4>Generosity</h4></div>
    <p>Generosity creates a virtuous cycle of goodwill, fostering a sense of unity and shared purpose among colleagues. By freely sharing knowledge, support, and resources, we uplift those around us and contribute to a collaborative environment where collective achievements flourish.</p></div>
</div>

<svg class="lower" width="1200" height="886" viewBox="0 0 1200 886" aria-hidden="true">
  <path d="M0 60 C260 0 500 120 800 60 C1000 20 1100 40 1200 20 L1200 886 L0 886Z" fill="#8d97aa"/>
  <path d="M0 120 C300 60 560 180 860 110 C1020 75 1120 90 1200 70 L1200 886 L0 886Z" fill="var(--wave)"/>
  <path d="M0 330 C300 290 600 380 900 320 C1050 290 1130 300 1200 290 L1200 886 L0 886Z" fill="var(--slate)"/>
</svg>

<div class="newsletter">
  <div><h2>Subscribe Our Newsletter</h2><p>Subscribe our newsletter to receive the latest news and exclusive offers every week. No spam.</p></div>
  <div class="subscribe">Enter email address<span class="go"></span></div>
</div>

<footer class="footer">
  <div><div class="brand">Veltrano</div><div class="socials"><span></span><span></span><span></span><span></span></div><span class="btn">CONTACT US</span></div>
  <div><h5>Quick links</h5><ul><li>Home</li><li>About Us</li><li>Services</li><li>Insights</li><li>Join Us</li><li>Contact Us</li></ul></div>
  <div><h5>Our Services</h5><ul><li>Business Transformation</li><li>ERP Implementations</li><li>ERP Solutions</li><li>IT and Data</li><li>Building the Right Team</li></ul></div>
  <div class="contact"><h5>Contact Info</h5><ul>
    <li><i></i><span>Email:<br>hello@veltrano.com</span></li>
    <li><i></i><span>Phone:<br>+1 (555) 013-2040</span></li>
    <li><i></i><span>Location:<br>128 Harbor Lane, Suite 4, Eastport</span></li></ul></div>
</footer>
<div class="copyright">© Veltrano Design 2023, All Rights Reserved</div>
<div class="chat"></div>
</body>
</html>
```